Medical consulting firm needs polished website

I am a physician and working on setting up a smal consulting firm in New Hampshire, USA. It is called Bright Harbor Medical Services, LLC and the website will be BrightHarborMed.com. I was puttering around at making my own website, and it just didn't come together nicely so I've decided to leave it to the pros. The focus of the business is Advanced Care Planning, ie planning for your future medical needs. So it deals with some heavy stuff like planning for if you get sick, who should make decisions for you, end of life options etc. So it can't be too flippant or cutesy, but also can't be too dour and dark. I am hoping to convey that by thinking ahead and making some plans you can lift some of the worries off of yourself and your family - and that we can help make a scary sounding path more manageable. I want it to be made with wordpress and I have actually already bought a template ( Vitarun – A Modern Multidisciplinary Medical & Health Theme ). The website needs to have general information about our services, doc profile, appointment maker, blog/url link page, and ideally web commerce application ( the template has access to woocommerce). I've posted my business card and current brochure (still tweaking them, but you get the idea). I am also partnering with lumenfold.com and so have included their logo and would want connections/info about them. I have the logos etc in different formats as needed.

Target Market(s)

middle aged to older adults

Industry/Entity Type

Medical

Coding

Coded - Design and coding required

Font styles to use
Sans Serif

Requirements
Must have
• as above.
Nice to have
• Ease of reading/access for elderly viewers. woo commerce.

```html
<!DOCTYPE html>
<html lang="en">
<head>
<meta charset="utf-8">
<title>Bright Harbor Medical Services</title>
<link href="https://fonts.googleapis.com/css2?family=Jost:wght@400;500;600;700&family=Open+Sans:ital,wght@0,400;0,600;1,400;1,600&display=swap" rel="stylesheet">
<style>
:root{
  --green:#3bb54a;
  --blue:#1d6fb8;
  --ink:#222;
  --text:#555;
  --muted:#888;
  --line:#e2e2e2;
  --band:#f4f4f4;
  --footer:#f3f3f3;
  --white:#fff;
}
*{box-sizing:border-box;margin:0;padding:0}
html,body{width:1200px;height:2980px;overflow:hidden;background:var(--white)}
body{position:relative;font-family:"Open Sans",Arial,sans-serif;color:var(--text)}
.abs{position:absolute}
.head-font{font-family:"Jost",Arial,sans-serif}

/* header */
.brand{left:100px;top:40px;display:flex;align-items:center;gap:12px}
.brand-dot{width:62px;height:62px;border-radius:50%;background:var(--blue)}
.brand-name{font-family:"Jost",sans-serif;font-size:30px;font-weight:500;color:var(--blue);line-height:1.05}
.contact{top:50px;display:flex;gap:14px;align-items:flex-start}
.contact small{display:block;font-size:12px;color:#444}
.contact b{display:block;font-size:14px;color:var(--blue);font-weight:600;margin-top:4px}
.contact svg{stroke:#777;fill:none;stroke-width:1.6}

/* nav */
.nav{left:0;top:142px;width:1200px;height:54px;border-top:1px solid var(--line);border-bottom:1px solid var(--line);display:flex;padding-left:98px}
.nav a{display:flex;align-items:center;justify-content:center;font-size:13px;color:#333;text-decoration:none;border-right:1px solid var(--line);position:relative}
.nav a:first-child{color:var(--blue)}
.nav a.active::after{content:"";position:absolute;left:0;right:0;bottom:-1px;height:4px;background:var(--blue)}
.nav a.cta{background:var(--green);color:var(--white);border:none}

/* hero */
.hero{left:0;top:197px;width:1200px;height:560px;background:linear-gradient(90deg,#e6e9ee 0%,#f3f3f3 60%,#fafafa 100%)}
.hero-photo{left:0;top:197px;width:780px;height:520px;background:radial-gradient(ellipse at 45% 45%,#c9ccd2 0%,#b7c3d8 40%,#e8eaee 85%)}
.hero-title{left:732px;top:298px;font-family:"Jost",sans-serif;font-size:54px;font-weight:400;color:#222}
.hero-sub{left:830px;top:362px;font-family:"Jost",sans-serif;font-size:38px;font-weight:700;color:#222;letter-spacing:1px}
.btn{display:inline-flex;align-items:center;justify-content:center;border:1px solid var(--green);color:var(--green);font-size:12px;background:var(--white)}
.btn.blue{border-color:var(--blue);color:var(--blue)}
.dots{left:886px;top:578px;display:flex;gap:14px}
.dots i{width:11px;height:11px;border-radius:50%;border:1px solid #999}
.dots i.on{background:var(--green);border-color:var(--green)}

/* welcome */
.band{left:0;top:757px;width:1200px;height:303px;background:var(--band)}
.section-title{width:1200px;left:0;text-align:center;font-family:"Jost",sans-serif;font-size:28px;font-weight:500;color:#222}
.lead{left:170px;width:860px;text-align:center;font-size:11px;line-height:23px;color:#666}
.feature{width:540px;text-align:center}
.ring{border-radius:50%;border:11px solid var(--green);background:var(--white);position:absolute}
.ring .pic{position:absolute;inset:5px;border-radius:50%}
.feature h3{font-size:13px;font-weight:600;color:#222}
.feature p{font-size:11px;line-height:20px;color:#666;margin:10px auto 0;width:500px}
.vdivider{width:1px;background:var(--line)}

/* services */
.service{width:340px;text-align:center}
.service h4{font-size:13px;font-weight:600;color:#222;line-height:22px}
.service p{font-size:11px;line-height:20px;color:#666;margin-top:8px}
.icon-ring{width:100px;height:100px;border-radius:50%;border:1px solid var(--blue);display:flex;align-items:center;justify-content:center}
.icon-ring svg{stroke:var(--blue);fill:none;stroke-width:2}
.chev{stroke:#bbb;fill:none;stroke-width:1.5}

/* testimonials */
.testi-photo{left:400px;top:1722px;width:800px;height:380px;background:linear-gradient(90deg,rgba(255,255,255,1) 0%,rgba(236,228,204,.6) 18%,#d9c98f 55%,#e9d9a4 100%)}
.quote-mark{font-family:"Jost",sans-serif;font-size:70px;color:#999;line-height:1}
.testi-text{left:100px;top:1858px;width:430px;font-size:13px;font-style:italic;font-weight:600;line-height:27px;color:#555}
.testi-name{left:100px;top:1968px;font-size:13px;color:var(--green)}
.bars{left:100px;top:2026px;display:flex;gap:8px}
.bars i{width:16px;height:3px;background:#ccc}
.bars i.on{background:var(--green)}

/* footer */
.footer{left:0;top:2626px;width:1200px;height:294px;background:var(--footer)}
.foot-brand{left:100px;top:2675px;display:flex;align-items:center;gap:10px}
.foot-brand .brand-dot{background:#9a9a9a;width:62px;height:62px}
.foot-brand .brand-name{color:#8a8a8a}
.foot-col-title{font-size:13px;font-weight:600;color:var(--blue);letter-spacing:.3px}
.tweet{display:flex;gap:10px;width:270px}
.tweet .bird{width:14px;height:14px;border-radius:50%;background:var(--blue);flex:none;margin-top:2px}
.tweet p{font-size:11px;line-height:20px;color:#555;font-style:italic}
.tweet p b{color:var(--blue);font-weight:400}
.tweet span{display:block;font-size:10px;color:var(--green);font-style:normal;margin-top:4px}
.field{width:276px;border-bottom:1px solid #ddd;height:34px;font-size:11px;color:#888;display:flex;align-items:center;gap:10px;padding-left:8px}
.field i{width:9px;height:9px;border-radius:50%;background:#aaa}
.partner{left:100px;top:2817px;width:214px;height:52px;border:1px solid #ccc;background:var(--white);display:flex;align-items:center;justify-content:center;gap:8px;font-size:24px;color:#333;font-weight:400}
.partner i{width:22px;height:22px;border-radius:50%;background:#333}
.copy{left:100px;top:2942px;font-size:11px;color:#666}
.follow{left:880px;top:2932px;display:flex;align-items:center;gap:10px;font-size:11px;color:#666}
.follow i{width:28px;height:28px;border-radius:50%;background:#bbb}
</style>
</head>
<body>

<!-- header -->
<div class="abs brand">
  <div class="brand-dot"></div>
  <div class="brand-name">Bright Harbor<br><span style="font-size:15px;letter-spacing:2px">MEDICAL SERVICES</span></div>
</div>
<div class="abs contact" style="left:706px">
  <svg width="20" height="36" viewBox="0 0 20 36"><rect x="2" y="2" width="16" height="32" rx="2"/><line x1="8" y1="29" x2="12" y2="29"/></svg>
  <div><small>Call Us Today!</small><b>603-555-0148</b></div>
</div>
<div class="abs contact" style="left:888px">
  <svg width="34" height="24" viewBox="0 0 34 24"><rect x="1" y="1" width="32" height="22"/><polyline points="1,1 17,13 33,1"/></svg>
  <div><small>E-mail</small><b>info@brightharbormed.com</b></div>
</div>

<nav class="abs nav">
  <a class="active" style="width:134px">Home</a>
  <a style="width:138px">About us</a>
  <a style="width:122px">Services</a>
  <a style="width:152px">Testimonials</a>
  <a style="width:108px">Blog</a>
  <a style="width:134px">Contact Us</a>
  <a class="cta" style="width:194px">Make an Appointment</a>
</nav>

<!-- hero -->
<div class="abs hero"></div>
<div class="abs hero-photo" role="img" aria-label="Photo of a smiling senior couple sitting together"></div>
<div class="abs hero-title">Advanced Care</div>
<div class="abs hero-sub">Planning</div>
<div class="abs" style="left:796px;top:448px;display:flex;gap:10px">
  <span class="btn" style="width:116px;height:38px">Read More Info</span>
  <span class="btn blue" style="width:120px;height:38px">Get Start Today</span>
</div>
<div class="abs dots"><i class="on"></i><i></i><i></i></div>
<svg class="abs" style="left:0;top:540px" width="1200" height="230" viewBox="0 0 1200 230">
  <path d="M0 50 C 260 210 640 200 1200 70 L1200 230 L0 230 Z" fill="#f4f4f4"/>
  <path d="M0 50 C 260 200 640 190 1200 70 L1200 90 C 640 215 260 225 0 75 Z" fill="#1d6fb8"/>
  <path d="M0 42 C 260 180 640 170 1200 62 L1200 74 C 640 190 260 200 0 60 Z" fill="#3bb54a"/>
</svg>

<!-- welcome -->
<div class="abs band"></div>
<h2 class="abs section-title" style="top:800px">Welcome to Brightharbormed</h2>
<p class="abs lead" style="top:850px">Sed ut perspiciatis unde omnis iste natus error sit voluptatem accusantium doloremque laudantium, totam rem aperiam, eaque ipsa quae ab illo inventore veritatis et quasi architecto beatae vitae dicta sunt explicabo. Nemo enim ipsam voluptatem quia voluptas sit aspernatur aut odit aut fugit, sed quia consequuntur magni dolores eos qui ratione voluptatem sequi nesciunt. Neque porro quisquam...</p>

<div class="ring" style="left:232px;top:968px;width:200px;height:200px"><div class="pic" role="img" aria-label="Photo of a family running together in a sunny park" style="background:radial-gradient(circle,#c9d6a0,#9bb070)"></div></div>
<div class="ring" style="left:770px;top:968px;width:200px;height:200px"><div class="pic" role="img" aria-label="Photo of an elderly couple embracing" style="background:radial-gradient(circle,#d8d4cf,#a9b3c4)"></div></div>

<div class="abs feature" style="left:62px;top:1180px">
  <h3>Neque porro quisquam</h3>
  <p>Sed quia non numquam eius modi tempora incidunt ut labore et dolore magnam aliquam quaerat voluptatem. Ut enim ad minima veniam, quis nostrum...</p>
  <span class="btn" style="width:118px;height:38px;margin-top:14px">Read More Info</span>
</div>
<div class="abs vdivider" style="left:602px;top:1130px;height:180px"></div>
<div class="abs feature" style="left:600px;top:1180px">
  <h3>Neque porro quisquam</h3>
  <p>Sed quia non numquam eius modi tempora incidunt ut labore et dolore magnam aliquam quaerat voluptatem. Ut enim ad minima veniam, quis nostrum...</p>
  <span class="btn" style="width:118px;height:38px;margin-top:14px">Read More Info</span>
</div>

<!-- services -->
<h2 class="abs section-title" style="top:1366px">Our Services</h2>
<svg class="abs chev" style="left:62px;top:1506px" width="20" height="62"><polyline points="18,2 2,31 18,60"/></svg>
<svg class="abs chev" style="left:1118px;top:1506px" width="20" height="62"><polyline points="2,2 18,31 2,60"/></svg>

<div class="abs icon-ring" style="left:200px;top:1436px"><svg width="48" height="44" viewBox="0 0 48 44"><path d="M6 20 L24 6 L42 20"/><path d="M12 16 V38 H36 V16"/><path d="M24 32 C16 26 18 20 24 23 C30 20 32 26 24 32Z"/></svg></div>
<div class="abs icon-ring" style="left:550px;top:1436px"><svg width="48" height="44" viewBox="0 0 48 44"><rect x="4" y="12" width="40" height="28" rx="3"/><path d="M17 12 V6 H31 V12"/><path d="M24 19 V33 M17 26 H31"/></svg></div>
<div class="abs icon-ring" style="left:900px;top:1436px"><svg width="48" height="48" viewBox="0 0 48 48"><path d="M12 6 V20 C12 30 28 30 28 20 V6"/><path d="M20 28 V36 C20 44 38 44 38 34 V26"/><circle cx="38" cy="22" r="4"/></svg></div>

<div class="vdivider abs" style="left:428px;top:1436px;height:220px"></div>
<div class="vdivider abs" style="left:778px;top:1436px;height:220px"></div>

<div class="abs service" style="left:80px;top:1554px">
  <h4>Individualized Physician-Guided<br>Healthcare planing</h4>
  <p>Totam rem aperiam, eaque ipsa quae ab illo veritatis etres quasi architecto beatae vitae dicta sunt...</p>
</div>
<div class="abs service" style="left:430px;top:1554px">
  <h4>Helping navigate complex medical<br>Situations</h4>
  <p>Totam rem aperiam, eaque ipsa quae ab illo veritatis etres quasi architecto beatae vitae dicta sunt...</p>
</div>
<div class="abs service" style="left:780px;top:1554px">
  <h4>Sharing your decisions with your loved<br>Ones and your doctors</h4>
  <p>Totam rem aperiam, eaque ipsa quae ab illo veritatis etres quasi architecto beatae vitae dicta sunt...</p>
</div>

<!-- testimonials -->
<div class="abs testi-photo" role="img" aria-label="Photo of a smiling senior couple with a bicycle in autumn leaves"></div>
<h2 class="abs head-font" style="left:100px;top:1752px;font-size:28px;font-weight:500;color:#222">Testimonials</h2>
<div class="abs quote-mark" style="left:96px;top:1818px">&ldquo;</div>
<p class="abs testi-text">&nbsp;&nbsp;&nbsp;&nbsp;&nbsp;&nbsp;Neque porro quisquam est, qui dolorem ipsum quia dolor sit amet, consectetur, adipisci velit, sed quia non numquam tempora incidunt ut labore et dolore magnam aliquam quaerat...</p>
<div class="abs quote-mark" style="left:458px;top:1926px">&rdquo;</div>
<div class="abs testi-name">-Marion &amp; family</div>
<div class="abs bars"><i class="on"></i><i></i><i></i></div>

<!-- blog -->
<h2 class="abs section-title" style="top:2148px">Latest Blog</h2>
<svg class="abs chev" style="left:352px;top:2290px" width="20" height="62"><polyline points="18,2 2,31 18,60"/></svg>
<svg class="abs chev" style="left:828px;top:2290px" width="20" height="62"><polyline points="2,2 18,31 2,60"/></svg>
<div class="ring" style="left:502px;top:2220px;width:196px;height:196px"><div class="pic" role="img" aria-label="Photo of a happy family of four together at home" style="background:radial-gradient(circle,#e2d2c2,#8f9fb5)"></div></div>
<h3 class="abs" style="left:0;width:1200px;text-align:center;top:2430px;font-size:13px;font-weight:600;color:#222">Neque porro quisquam est, qui dolorem ipsum quia dolor sit amet</h3>
<p class="abs" style="left:130px;width:940px;text-align:center;top:2458px;font-size:11px;line-height:22px;color:#666">Sed quia non numquam eius modi tempora incidunt ut labore et dolore magnam aliquam quaerat voluptatem. Ut enim ad minima veniam, quis nostrumeus modi tempora non incidunt ut labore numquam eius modi tempora incidunt ut labore et dolore magnam aliquam quaerat voluptatem....</p>
<span class="abs btn" style="left:536px;top:2516px;width:130px;height:38px">23,October,2016</span>

<!-- footer -->
<div class="abs footer"></div>
<div class="abs foot-brand">
  <div class="brand-dot"></div>
  <div class="brand-name">Bright Harbor<br><span style="font-size:15px;letter-spacing:2px">MEDICAL SERVICES</span></div>
</div>
<p class="abs" style="left:100px;top:2752px;width:270px;font-size:11px;line-height:21px;color:#555">Quia dolor sit amet, consectetur, adipisci velit, sed quia non numquam eius modi tempora...</p>
<div class="abs partner"><i></i>lumenfold</div>

<div class="abs foot-col-title" style="left:458px;top:2670px">LATEST TWEETS</div>
<div class="abs tweet" style="left:458px;top:2708px">
  <div class="bird"></div>
  <p><b>@brightharbormed</b> t is a long established fact that a reader will be looking layout...<span>2 month ago</span></p>
</div>
<div class="abs" style="left:484px;top:2780px;width:250px;height:1px;background:#ddd"></div>
<div class="abs tweet" style="left:458px;top:2788px">
  <div class="bird"></div>
  <p><b>@brightharbormed</b> t is a long established fact that a reader will be looking layout...<span>2 month ago</span></p>
</div>

<div class="abs foot-col-title" style="left:830px;top:2670px">NEWSLETTER</div>
<div class="abs field" style="left:830px;top:2704px"><i></i>Enter your Name</div>
<div class="abs field" style="left:830px;top:2750px"><i></i>Enter your E-Mail Address</div>
<span class="abs btn" style="left:830px;top:2814px;width:72px;height:30px;font-size:11px">SIGN UP</span>

<div class="abs copy">Copyrights &copy; brightharbormed . 2016 | Allrights Reserved.</div>
<div class="abs follow">Follow Us : <i></i><i></i><i></i><i></i></div>

</body>
</html>
```